Wordpress theme website for professionals working together

My partner and I are offering business services, my wife in the energy business as mainly as member of the board of commissioners. I am working as interim manager/consultant in the accounting and finance area. Both activities are connected in one company VELMOT BV (dutch ltd). We need a CV based website. Beside this we do some financial and accounting services.

Target Market(s)

small medium business

Font styles to use
Sans Serif

Colors

Designer to choose colors to be used in the design.

Requirements
Must have
• Pictures of both members.
• CLEAN AND SIMPLE
• I LIKE BLACK & WHITE
Nice to have
• I like design like this theme: http://theme.pruxelo-example.com/resume/

```html
<!DOCTYPE html>
<html lang="en">
<head>
<meta charset="utf-8">
<title>VELMOT BV</title>
<link rel="stylesheet" href="https://fonts.googleapis.com/css2?family=Roboto+Slab:wght@300;400&family=Arimo:wght@400;700&display=swap">
<style>
:root{
  --ink:#222222;
  --text:#444444;
  --muted:#555555;
  --paper:#ffffff;
  --soft:#f4f4f4;
  --night:#111111;
  --bar-fill:#9a9a9a;
  --bar-rest:#ffffff;
  --line:#bdbdbd;
  --light-text:#d8d8d8;
}
*{margin:0;padding:0;box-sizing:border-box}
html,body{width:1200px;height:2748px;overflow:hidden;background:var(--paper)}
body{position:relative;font-family:"Arimo",Arial,sans-serif;color:var(--text)}
.slab{font-family:"Roboto Slab",Georgia,serif}
.abs{position:absolute}

/* header */
.site-header{position:absolute;left:0;top:0;width:1200px;height:108px;background:var(--paper);box-shadow:0 1px 4px rgba(0,0,0,.12);z-index:2}
.brand{position:absolute;left:112px;top:38px;font-family:"Roboto Slab",Georgia,serif;font-size:29px;font-weight:400;color:var(--ink);letter-spacing:.5px}
.main-nav a{position:absolute;top:48px;font-family:"Roboto Slab",Georgia,serif;font-size:14px;color:var(--ink);text-decoration:none}

/* hero */
.hero{position:absolute;left:0;top:108px;width:1200px;height:550px;background:linear-gradient(90deg,#cfd2d8 0%,#e0e2e6 35%,#d8d9dc 55%,#bfbcb8 100%)}
.hero-photo{position:absolute;left:531px;top:0;width:669px;height:550px;background:radial-gradient(ellipse at 60% 45%,#c9a08e 0%,#b48d7c 30%,#6f6a6d 60%,#2c2f3a 100%)}
.hero-title{position:absolute;left:112px;top:118px;font-family:"Roboto Slab",Georgia,serif;font-weight:300;font-size:70px;color:#333;letter-spacing:1px}
.hero-text{position:absolute;left:112px;top:220px;width:450px;font-family:"Roboto Slab",Georgia,serif;font-size:13px;line-height:34px;color:#333}
.btn-pill{position:absolute;left:112px;top:350px;width:139px;height:46px;border:1px solid #999;border-radius:23px;font-family:"Roboto Slab",Georgia,serif;font-size:16px;color:#333;display:flex;align-items:center;justify-content:center}

/* person tabs */
.tab{position:absolute;top:698px;width:170px;height:51px;border-radius:26px;font-family:"Roboto Slab",Georgia,serif;font-size:20px;display:flex;align-items:center;justify-content:center}
.tab-idle{left:425px;border:1px solid #aaa;color:#444;background:var(--paper)}
.tab-active{left:606px;background:#3a3a3a;color:#fff}
.tab-active::after{content:"";position:absolute;left:77px;bottom:-8px;border:8px solid transparent;border-bottom:0;border-top-color:#3a3a3a}

/* profile */
.profile{position:absolute;left:0;top:788px;width:1200px;height:467px;background:var(--soft)}
.avatar{position:absolute;left:121px;top:42px;width:140px;height:140px;border-radius:50%;border:4px solid #d0d0d0;background:radial-gradient(circle at 50% 40%,#d9a582 0%,#b8704a 55%,#6b3a26 100%)}
.profile-name{position:absolute;left:288px;top:50px;font-family:"Roboto Slab",Georgia,serif;font-size:25px;color:var(--ink)}
.timeline{position:absolute;left:292px;top:119px;width:2px;height:140px;background:#999}
.dot-full{position:absolute;left:287px;top:114px;width:12px;height:12px;border-radius:50%;background:#666}
.dot-open{position:absolute;left:287px;top:252px;width:12px;height:12px;border-radius:50%;background:var(--soft);border:2px solid #666}
.job-group{position:absolute;left:313px;font-family:"Roboto Slab",Georgia,serif;font-size:17px;color:#333}
.job{position:absolute;left:454px}
.job-title{font-size:14px;font-weight:700;color:var(--ink)}
.job-desc{margin-top:10px;font-size:12px;color:var(--muted)}

/* skills */
.skills{position:absolute;left:0;top:1255px;width:1200px;height:489px;background:var(--night)}
.skills-title{position:absolute;left:156px;top:32px;font-family:"Roboto Slab",Georgia,serif;font-size:27px;color:#fff}
.skill{position:absolute;left:253px;width:786px}
.skill-label{font-size:12px;color:var(--light-text)}
.skill-bar{position:relative;margin-top:14px;height:7px;border-radius:4px;background:var(--bar-rest);overflow:visible}
.skill-fill{position:absolute;left:0;top:0;height:7px;border-radius:4px 0 0 4px;background:var(--bar-fill)}
.skill-tag{position:absolute;top:-27px;transform:translateX(-50%);padding:2px 4px;border:1px solid #bbb;font-size:10px;color:#ddd;background:var(--night)}

/* education */
.education{position:absolute;left:0;top:1744px;width:1200px;height:218px;background:var(--soft)}
.section-title{position:absolute;left:0;width:1200px;text-align:center;font-family:"Roboto Slab",Georgia,serif;font-size:32px;color:var(--ink)}
.edu-chip{position:absolute;top:114px;width:130px;height:36px;border:1px solid #aaa;background:var(--paper);font-size:12px;color:#333;display:flex;align-items:center;justify-content:center}

/* worked for */
.worked{position:absolute;left:0;top:1962px;width:1200px;height:473px;background:var(--night)}
.worked-title{position:absolute;left:123px;top:58px;font-family:"Roboto Slab",Georgia,serif;font-size:26px;color:#fff}
.worked-intro{position:absolute;left:288px;top:55px;width:760px;font-size:12px;line-height:25px;color:var(--light-text)}
.client{position:absolute;top:157px}
.client-name{font-family:"Roboto Slab",Georgia,serif;font-size:20px;color:#fff}
.ticks{list-style:none;margin-top:22px}
.ticks li{position:relative;padding-left:30px;height:38.5px;font-size:12px;color:var(--light-text)}
.ticks svg{position:absolute;left:0;top:2px}

/* reading */
.reading{position:absolute;left:0;top:2435px;width:1200px;height:230px;background:var(--soft)}
.reading-text{position:absolute;left:230px;top:102px;width:740px;text-align:center;font-size:12px;line-height:28.5px;color:var(--muted)}

/* footer */
.site-footer{position:absolute;left:0;top:2665px;width:1200px;height:83px;background:var(--paper)}
.copyright{position:absolute;left:112px;top:34px;font-family:"Roboto Slab",Georgia,serif;font-size:13px;color:#555}
.social{position:absolute;left:879px;top:24px;display:flex;gap:8px}
.social span{width:36px;height:36px;border-radius:50%;border:1px solid #999}
</style>
</head>
<body>

<header class="site-header">
  <div class="brand">VELMOT BV</div>
  <nav class="main-nav">
    <a style="left:603px">Home</a>
    <a style="left:680px">About Us</a>
    <a style="left:777px">Job</a>
    <a style="left:841px">Skills</a>
    <a style="left:918px">Education</a>
    <a style="left:1020px">Contact Us</a>
  </nav>
</header>

<section class="hero">
  <div class="hero-photo" role="img" aria-label="Portrait photo of Pieter, smiling, wearing glasses and a dark jacket"></div>
  <h1 class="hero-title">VELMOT BV</h1>
  <p class="hero-text">Sed ut perspiciatis unde omnis iste natus error sit voluptatem accusantium doloremque laudantium, totam rem aperiam, eaque ipsa quae ab illo invento quasi architecto beatae vitae dicta sunt explicabo.</p>
  <div class="btn-pill">Read More</div>
</section>

<div class="tab tab-idle">Pieter</div>
<div class="tab tab-active">Marit</div>

<section class="profile">
  <div class="avatar" role="img" aria-label="Portrait photo of Marit"></div>
  <h2 class="profile-name">Marit</h2>
  <div class="timeline"></div>
  <div class="dot-full"></div>
  <div class="dot-open"></div>
  <div class="job-group" style="top:109px">Actual Jobs :</div>
  <div class="job-group" style="top:247px">Finished Jobs :</div>

  <div class="job" style="top:113px"><div class="job-title">Director Voltara</div><div class="job-desc">Sed ut perspiciatis unde omnis iste natus error sit voluptatem accusantium doloremque laudantium</div></div>
  <div class="job" style="top:173px"><div class="job-title">Netvion</div><div class="job-desc">Sed ut perspiciatis unde omnis iste natus error sit voluptatem accusantium</div></div>
  <div class="job" style="top:250px"><div class="job-title">Director Gasmeridian</div><div class="job-desc">Sed ut perspiciatis unde omnis iste natus error sit voluptatem accusantium</div></div>
  <div class="job" style="top:311px"><div class="job-title">Advisor Gas</div><div class="job-desc">Sed ut perspiciatis unde omnis iste natus error sit voluptatem</div></div>
  <div class="job" style="top:371px"><div class="job-title">Oipoip o kklijk</div><div class="job-desc">Sed ut perspiciatis unde omnis iste natus</div></div>
</section>

<section class="skills">
  <h2 class="skills-title">Skills :</h2>
  <div class="skill" style="top:43px"><div class="skill-label">General management</div><div class="skill-bar"><div class="skill-fill" style="width:62%"></div><span class="skill-tag" style="left:62%">65%</span></div></div>
  <div class="skill" style="top:105px"><div class="skill-label">Energy knowledge</div><div class="skill-bar"><div class="skill-fill" style="width:88%"></div><span class="skill-tag" style="left:88%">85%</span></div></div>
  <div class="skill" style="top:166px"><div class="skill-label">Gas knowledge</div><div class="skill-bar"><div class="skill-fill" style="width:78%"></div><span class="skill-tag" style="left:78%">75%</span></div></div>
  <div class="skill" style="top:228px"><div class="skill-label">People management</div><div class="skill-bar"><div class="skill-fill" style="width:62%"></div><span class="skill-tag" style="left:62%">65%</span></div></div>
  <div class="skill" style="top:290px"><div class="skill-label">Project management</div><div class="skill-bar"><div class="skill-fill" style="width:52%"></div><span class="skill-tag" style="left:52%">50%</span></div></div>
  <div class="skill" style="top:351px"><div class="skill-label">Team player</div><div class="skill-bar"><div class="skill-fill" style="width:39%"></div><span class="skill-tag" style="left:38%">30%</span></div></div>
  <div class="skill" style="top:411px"><div class="skill-label">Trouble shooter</div><div class="skill-bar"><div class="skill-fill" style="width:78%"></div><span class="skill-tag" style="left:78%">85%</span></div></div>
</section>

<section class="education">
  <h2 class="section-title" style="top:46px">Education</h2>
  <div class="edu-chip" style="left:462px">KVU</div>
  <div class="edu-chip" style="left:608px">Lyceum C</div>
</section>

<section class="worked">
  <h2 class="worked-title">Worked for :</h2>
  <p class="worked-intro">Sed ut perspiciatis unde omnis iste natus error sit voluptatem accusantium doloremque laudantium, quae ab illo inventore veritatis et quasi ab illo inventore veritatis et quasi architecto beatae vitae dicta sunt architecto beatae vitae dicta sunt explicabo.</p>

  <div class="client" style="left:286px">
    <h3 class="client-name">Gasmeridian</h3>
    <ul class="ticks">
      <li><svg width="11" height="10" viewBox="0 0 11 10"><path d="M1 5l3 3 6-7" fill="none" stroke="#ddd" stroke-width="2"/></svg>Sed ut perspiciatis unde omnis iste natus</li>
      <li><svg width="11" height="10" viewBox="0 0 11 10"><path d="M1 5l3 3 6-7" fill="none" stroke="#ddd" stroke-width="2"/></svg>Error sit voluptatem accusantium</li>
      <li><svg width="11" height="10" viewBox="0 0 11 10"><path d="M1 5l3 3 6-7" fill="none" stroke="#ddd" stroke-width="2"/></svg>Doloremque laudantium, totam</li>
      <li><svg width="11" height="10" viewBox="0 0 11 10"><path d="M1 5l3 3 6-7" fill="none" stroke="#ddd" stroke-width="2"/></svg>Rem aperiam, eaque ipsa quae ab</li>
      <li><svg width="11" height="10" viewBox="0 0 11 10"><path d="M1 5l3 3 6-7" fill="none" stroke="#ddd" stroke-width="2"/></svg>Beatae vitae dicta sunt explicabo</li>
    </ul>
  </div>

  <div class="client" style="left:687px">
    <h3 class="client-name">KVU</h3>
    <ul class="ticks">
      <li><svg width="11" height="10" viewBox="0 0 11 10"><path d="M1 5l3 3 6-7" fill="none" stroke="#ddd" stroke-width="2"/></svg>Sed ut perspiciatis unde omnis iste natus</li>
      <li><svg width="11" height="10" viewBox="0 0 11 10"><path d="M1 5l3 3 6-7" fill="none" stroke="#ddd" stroke-width="2"/></svg>Error sit voluptatem accusantium</li>
      <li><svg width="11" height="10" viewBox="0 0 11 10"><path d="M1 5l3 3 6-7" fill="none" stroke="#ddd" stroke-width="2"/></svg>Doloremque laudantium, totam</li>
      <li><svg width="11" height="10" viewBox="0 0 11 10"><path d="M1 5l3 3 6-7" fill="none" stroke="#ddd" stroke-width="2"/></svg>Rem aperiam, eaque ipsa quae ab</li>
      <li><svg width="11" height="10" viewBox="0 0 11 10"><path d="M1 5l3 3 6-7" fill="none" stroke="#ddd" stroke-width="2"/></svg>Beatae vitae dicta sunt explicabo</li>
    </ul>
  </div>
</section>

<section class="reading">
  <h2 class="section-title" style="top:44px">Reading</h2>
  <p class="reading-text">Sed ut perspiciatis unde omnis iste natus error sit voluptatem accusantium doloremque laudantium, totam rem aperiam, eaque ipsa quae ab illo inventore veritatis et quasi architecto beatae vitae dicta sunt explicabo. Nemo enim ipsam voluptatem quia voluptas sit aspernatur sed quia consequuntur magni dolores eos qui ratione voluptatem sequi nesciunt.</p>
</section>

<footer class="site-footer">
  <div class="copyright">© Copyright-2018 VELMOT BV.All rights reserved.</div>
  <div class="social" role="img" aria-label="Social media links">
    <span></span><span></span><span></span><span></span><span></span>
  </div>
</footer>

</body>
</html>
```